Website for Briar Hollow Gathering Church

Wordpress website design required for Briar Hollow Gathering Church. We are a family oriented church catering for age groups from school age to elderly people. The church has a wide variety of activities which it coordinates. The idea is to describe the activities on the activities page, but cross-link them to show which would be applicable to the different age groups.

We would like an inviting website which is easy to read and navigate.

Target Market(s)

Very wide audience - from school age youth to elderly people, so design and style should cater for both audiences.

Industry/Entity Type

Church

Coding

Coded - Design and coding required

Number of Pages Required

5+ page

Font styles to use
Sans Serif

Colors
0255a3
ffffff
0792cd
f78f20

Requirements
Must have
• Inviting website.
• Clear readable font.
• Space to import photos to balance text on each page.
• Need to project a dynamic and progressive feel for the church.
• Easy to navigate.
Nice to have
• Scrolling photos on pages. Ability to enter questions/ comments/prayer requests on Home page.
Should not have
• Conservative audience, so should not be too bold.

```html
<!DOCTYPE html>
<html lang="en">
<head>
<meta charset="utf-8">
<title>Briar Hollow Gathering Church</title>
<link href="https://fonts.googleapis.com/css2?family=Open+Sans:wght@400;600;700&family=Quattrocento:wght@400;700&display=swap" rel="stylesheet">
<style>
:root{
  --navy:#0255a3;
  --nav-bar:#0b4394;
  --sky:#0792cd;
  --panel:#1580c4;
  --orange:#f78f20;
  --orange-dark:#e0741a;
  --white:#ffffff;
  --ink:#2b2b2b;
  --muted:#666666;
  --line:#dddddd;
  --grey-band:#e9e9e9;
  --serif:"Quattrocento", Georgia, serif;
  --sans:"Open Sans", Arial, sans-serif;
}
*{box-sizing:border-box;margin:0;padding:0}
html,body{width:1200px;height:2941px;overflow:hidden;background:var(--white)}
body{font-family:var(--sans);color:var(--ink);position:relative}
.abs{position:absolute}
/* header */
.site-header{position:absolute;left:0;top:0;width:1200px;height:175px}
.nav-bar{position:absolute;left:0;top:108px;width:1200px;height:67px;background:var(--nav-bar)}
.brand{position:absolute;left:112px;top:0;width:353px;height:175px;background:var(--white);display:flex;align-items:center;justify-content:center;gap:10px;padding-top:50px}
.brand-dot{width:14px;height:14px;border-radius:50%;background:var(--navy)}
.brand-name{font-family:var(--sans);font-weight:600;font-size:17px;color:var(--navy)}
.search{position:absolute;left:855px;top:28px;width:233px;height:52px;background:#eeeeee;border:1px solid #d6d6d6;display:flex;align-items:center;justify-content:space-between;padding:0 18px;font-size:12px;color:#888}
.main-nav{position:absolute;left:508px;top:108px;height:67px;display:flex}
.main-nav a{color:var(--white);text-decoration:none;font-size:12.5px;font-weight:600;padding:0 20px;line-height:67px;position:relative}
.main-nav a.active::after{content:"";position:absolute;left:8px;right:8px;bottom:0;height:4px;background:var(--sky)}
/* hero */
.hero{position:absolute;left:0;top:175px;width:1200px;height:490px;background:linear-gradient(90deg,#3a2a22 0%,#bdb7b0 30%,#e4e0dc 50%,#9b8c80 75%,#3b2a20 100%)}
.hero-card{position:absolute;left:288px;top:93px;width:624px;height:304px;background:rgba(255,255,255,.8);text-align:center;padding-top:42px}
.hero-card .kicker{font-size:24px;color:#333;letter-spacing:.5px}
.hero-card h1{font-family:var(--serif);font-weight:400;color:var(--navy);font-size:40px;line-height:52px;margin-top:10px}
.hero-arrow{position:absolute;top:243px;width:38px;height:38px;background:rgba(255,255,255,.75);display:flex;align-items:center;justify-content:center}
/* message */
.message-pointer{position:absolute;left:580px;top:702px}
.message{position:absolute;left:112px;top:735px;width:976px;height:260px;background:var(--panel);color:var(--white);text-align:center}
.message h2{font-family:var(--serif);font-weight:400;font-size:31px;margin-top:60px}
.message p{font-size:11.5px;line-height:25px;width:730px;margin:20px auto 0}
.quote-mark{position:absolute;left:78px;top:80px;font-family:var(--serif);font-size:110px;line-height:1;color:rgba(255,255,255,.35)}
/* news */
.section-title{position:absolute;left:0;width:1200px;text-align:center;font-family:var(--serif);font-weight:400;font-size:31px;color:#222}
.photo{position:absolute}
.date-box{position:absolute;left:112px;top:1490px;width:88px;height:82px;background:var(--orange);color:var(--white);text-align:center}
.date-box .day{font-size:34px;line-height:44px;padding-top:4px}
.date-box .mon{font-size:18px;line-height:22px}
.news-title{font-weight:700;font-size:15px;line-height:25px;color:#222}
.meta{display:flex;align-items:center;gap:6px;font-size:11.5px;color:#444}
.meta svg{flex:none}
.news-text{font-size:11.5px;line-height:25px;color:var(--muted)}
.read-more{font-size:11.5px;color:var(--orange);text-transform:uppercase}
.news-rule{position:absolute;left:612px;width:478px;height:1px;background:var(--line)}
/* prayer */
.prayer{position:absolute;left:0;top:1753px;width:1200px;height:450px;background:linear-gradient(180deg,#163f8e 0%,#2358a6 50%,#325f8e 80%,#3a5a70 100%);color:var(--white);text-align:center}
.prayer h2{font-family:var(--serif);font-weight:400;font-size:31px;margin-top:125px}
.prayer p{font-size:11.5px;line-height:25px;width:860px;margin:20px auto 0}
.pill-input{position:absolute;left:323px;top:270px;width:362px;height:57px;border-radius:29px;background:var(--white);color:#999;font-size:11.5px;text-align:left;padding:20px 0 0 20px}
.pill-btn{position:absolute;background:linear-gradient(180deg,var(--orange),var(--orange-dark));color:var(--white);border-radius:30px;text-align:center;font-weight:600}
/* contact */
.contact{position:absolute;left:0;top:2203px;width:1200px;height:250px;background:var(--grey-band)}
.contact-item{position:absolute;top:122px;display:flex;align-items:center;gap:14px;font-size:12.5px;color:#333}
.icon-circle{width:58px;height:58px;border-radius:50%;background:var(--orange);display:flex;align-items:center;justify-content:center}
/* footer */
.col-title{position:absolute;top:2507px;font-family:var(--serif);font-size:22px;color:#222}
.field{position:absolute;border:1px solid #c8c8c8;font-size:11.5px;color:#888;padding:18px 0 0 16px}
.times{position:absolute;left:550px;top:2558px;width:268px}
.times .row{display:flex;justify-content:space-between;font-size:11.5px;color:#444;height:53px;align-items:center;border-bottom:1px solid #cfcfcf}
.mission{position:absolute;left:872px;top:2555px;width:218px;font-size:11.5px;line-height:25px;color:#444}
.footer-rule{position:absolute;left:112px;top:2828px;width:976px;height:1px;background:#cfcfcf}
.copyright{position:absolute;left:112px;top:2873px;font-size:11.5px;color:#444}
.social-badge{position:absolute;left:985px;top:2866px;width:103px;height:32px;background:#d8dbe4;border:1px solid #b6bccb}
</style>
</head>
<body>

<header class="site-header">
  <div class="nav-bar"></div>
  <div class="brand"><span class="brand-dot"></span><span class="brand-name">Briar Hollow Gathering Church</span></div>
  <div class="search">Search...
    <svg width="12" height="12" viewBox="0 0 12 12"><circle cx="5" cy="5" r="3.8" fill="none" stroke="#777" stroke-width="1.5"/><line x1="8" y1="8" x2="11" y2="11" stroke="#777" stroke-width="1.6"/></svg>
  </div>
  <nav class="main-nav">
    <a class="active">HOME</a><a>AGE GROUP</a><a>ACTIVITES</a><a>EVENTS</a><a>ABOUT BHGC</a><a>CONTACT</a>
  </nav>
</header>

<section class="hero" role="img" aria-label="Photo of wooden church pews in soft light">
  <div class="hero-card">
    <div class="kicker">WELCOME TO</div>
    <h1>BRIAR HOLLOW GATHERING<br>CHURCH</h1>
  </div>
  <div class="hero-arrow" style="left:30px"><svg width="10" height="14" viewBox="0 0 10 14"><path d="M8 1 2 7l6 6" fill="none" stroke="#555" stroke-width="2"/></svg></div>
  <div class="hero-arrow" style="left:1132px"><svg width="10" height="14" viewBox="0 0 10 14"><path d="M2 1l6 6-6 6" fill="none" stroke="#555" stroke-width="2"/></svg></div>
</section>

<svg class="message-pointer" width="40" height="34" viewBox="0 0 40 34"><path d="M20 0 40 34H0z" fill="var(--panel)"/></svg>
<section class="message">
  <div class="quote-mark">&ldquo;</div>
  <h2>CHURCH MESSAGE</h2>
  <p>Sed nibh enim, viverra ac egestas sit amet, lacinia id arcu. Donec feugiat, felis placerat blandit mollis, leo diam malesuada magna, in lobortis lorem dui quis lorem. Etiam elit odio, vulputate id metus a, luctus dignissim sapien. Etiam eu magna erat. Integer at magna quis nunc sceler isque tempor at a lorem.</p>
</section>

<h2 class="section-title" style="top:1054px">LATEST NEWS</h2>

<div class="photo" style="left:112px;top:1140px;width:476px;height:313px;background:linear-gradient(135deg,#2a1a12,#8a4a1e 45%,#e0903a 60%,#3a2418)" role="img" aria-label="Photo of a cathedral interior with stained glass windows"></div>
<div class="date-box"><div class="day">22</div><div class="mon">OCT</div></div>
<div class="abs" style="left:220px;top:1487px;width:370px">
  <div class="news-title">Vivamus feugiat eu leo vitae tempor. Proin scelerisque odio mi, at dignissim est dapibus in.</div>
  <div class="meta" style="margin-top:10px">
    <svg width="12" height="11" viewBox="0 0 12 11"><path d="M1 1h10v6H5l-3 3V7H1z" fill="var(--navy)"/></svg><span>24</span>
    <svg style="margin-left:18px" width="12" height="11" viewBox="0 0 12 11"><path d="M1 1h10v6H5l-3 3V7H1z" fill="var(--navy)"/></svg><span>Post Your Comments</span>
  </div>
</div>
<div class="abs news-text" style="left:112px;top:1590px;width:476px">Sed nibh enim, viverra ac egestas sit amet, lacinia id arcu. Donec feugiat, felis placerat blandit mollis, leo diam malesuada magna, in lobortis lorem dui quis lorem.</div>
<div class="abs read-more" style="left:112px;top:1653px">&raquo; Read more</div>

<div class="photo" style="left:612px;top:1140px;width:181px;height:140px;background:linear-gradient(135deg,#6a3a22,#b07a50,#4a2a1a)" role="img" aria-label="Photo of a congregation singing"></div>
<div class="photo" style="left:612px;top:1333px;width:181px;height:140px;background:linear-gradient(180deg,#c89a6a,#7a4a2a 60%,#3a2010)" role="img" aria-label="Photo of a church nave with pews"></div>
<div class="photo" style="left:612px;top:1527px;width:181px;height:140px;background:linear-gradient(135deg,#3a1a12,#a05030 50%,#2a140c)" role="img" aria-label="Photo of hands folded in prayer over a book"></div>

<div class="abs" style="left:823px;top:1137px;width:270px">
  <div class="news-title" style="font-size:14px">Vivamus feugiat eu leo vitae tempor.</div>
  <div class="meta" style="margin-top:8px"><svg width="11" height="11" viewBox="0 0 11 11"><rect x="0.5" y="1.5" width="10" height="9" fill="none" stroke="var(--navy)"/><rect x="0.5" y="1.5" width="10" height="3" fill="var(--navy)"/></svg><span>20 Oct, 2016</span><svg style="margin-left:12px" width="12" height="11" viewBox="0 0 12 11"><path d="M1 1h10v6H5l-3 3V7H1z" fill="var(--navy)"/></svg><span>24</span></div>
  <div class="news-text" style="margin-top:8px">Donec feugiat, felis placerat blandit mollis, leo diam malesuada magna, in lobortis.</div>
  <div class="read-more" style="margin-top:8px">&raquo; Read more</div>
</div>
<div class="news-rule" style="top:1310px"></div>
<div class="abs" style="left:823px;top:1330px;width:270px">
  <div class="news-title" style="font-size:14px">Morbi tempor molestie sagittis</div>
  <div class="meta" style="margin-top:8px"><svg width="11" height="11" viewBox="0 0 11 11"><rect x="0.5" y="1.5" width="10" height="9" fill="none" stroke="var(--navy)"/><rect x="0.5" y="1.5" width="10" height="3" fill="var(--navy)"/></svg><span>20 Oct, 2016</span><svg style="margin-left:12px" width="12" height="11" viewBox="0 0 12 11"><path d="M1 1h10v6H5l-3 3V7H1z" fill="var(--navy)"/></svg><span>24</span></div>
  <div class="news-text" style="margin-top:8px">Donec feugiat, felis placerat blandit mollis, leo diam malesuada magna, in lobortis.</div>
  <div class="read-more" style="margin-top:8px">&raquo; Read more</div>
</div>
<div class="news-rule" style="top:1503px"></div>
<div class="abs" style="left:823px;top:1523px;width:270px">
  <div class="news-title" style="font-size:14px">Duis fringilla elit at vestibulum pulvinar</div>
  <div class="meta" style="margin-top:8px"><svg width="11" height="11" viewBox="0 0 11 11"><rect x="0.5" y="1.5" width="10" height="9" fill="none" stroke="var(--navy)"/><rect x="0.5" y="1.5" width="10" height="3" fill="var(--navy)"/></svg><span>20 Oct, 2016</span><svg style="margin-left:12px" width="12" height="11" viewBox="0 0 12 11"><path d="M1 1h10v6H5l-3 3V7H1z" fill="var(--navy)"/></svg><span>24</span></div>
  <div class="news-text" style="margin-top:8px">Donec feugiat, felis placerat blandit mollis, leo diam malesuada magna, in lobortis.</div>
  <div class="read-more" style="margin-top:8px">&raquo; Read more</div>
</div>

<section class="prayer" role="img" aria-label="Photo of a person with raised arms under an evening sky, tinted blue">
  <h2>PRAYER REQUEST</h2>
  <p>Interdum et malesuada fames ac ante ipsum primis in faucibus. Pellentesque mollis nulla maximus neque convallis vulputate. Sed a semper purus. Maecenas mattis euismod neque at scelerisque. Fusce a ornare neque. Duis finibus quam eu blandit vestibulum.</p>
  <div class="pill-input">Email Address</div>
  <div class="pill-btn" style="left:705px;top:267px;width:170px;height:60px;line-height:60px;font-size:19px">SUBMIT</div>
</section>

<section class="contact">
  <h2 class="section-title" style="top:50px">CONTACT</h2>
  <div class="contact-item" style="left:233px"><span class="icon-circle"><svg width="16" height="22" viewBox="0 0 16 22"><path d="M8 0a8 8 0 0 0-8 8c0 6 8 14 8 14s8-8 8-14a8 8 0 0 0-8-8z" fill="#fff"/><circle cx="8" cy="8" r="3" fill="var(--orange)"/></svg></span>134, Lorem Ipsm, Loreum - 123 456</div>
  <div class="contact-item" style="left:557px"><span class="icon-circle"><svg width="20" height="20" viewBox="0 0 20 20"><path d="M4 1l4 4-2 3c1 2 3 4 6 6l3-2 4 4-3 3C8 19 1 12 1 4z" fill="#fff"/></svg></span>(000) 323 654 987</div>
  <div class="contact-item" style="left:761px"><span class="icon-circle"><svg width="22" height="16" viewBox="0 0 22 16"><rect width="22" height="16" rx="2" fill="#fff"/><path d="M1 2l10 7 10-7" fill="none" stroke="var(--orange)" stroke-width="1.8"/></svg></span>info@domainname.com</div>
</section>

<h3 class="col-title" style="left:112px">SEND MAIL</h3>
<div class="field" style="left:112px;top:2558px;width:180px;height:52px">Name</div>
<div class="field" style="left:318px;top:2558px;width:180px;height:52px">Email Address</div>
<div class="field" style="left:112px;top:2628px;width:386px;height:88px">Message</div>
<div class="pill-btn" style="left:385px;top:2737px;width:110px;height:42px;line-height:42px;font-size:11.5px">SUBMIT</div>

<h3 class="col-title" style="left:550px">SERVICE TIMES</h3>
<div class="times">
  <div class="row"><span>Monday &nbsp;- &nbsp;Friday</span><span>9.00 AM to &nbsp;6.00 PM</span></div>
  <div class="row"><span>Saturday</span><span>9.00 AM to &nbsp;3.00 PM</span></div>
  <div class="row"><span>Sunday</span><span>9.00 AM to &nbsp;2.00 PM</span></div>
</div>

<h3 class="col-title" style="left:872px">OUR MISSION</h3>
<p class="mission">Interdum et malesuada fames ac ante ipsum primis in faucibus. Pellentesque mollis nulla maximus neque convallis vu lputate. Sed a semper purus. Maecenas mattis euismod neque at scelerisque. Fusce a ornare neque. Duis finibus quam eu blandit vestibulum...</p>

<div class="footer-rule"></div>
<p class="copyright">Copyright &copy; 2016 Briar Hollow Gathering Church.All Right Reserved.</p>
<div class="social-badge"></div>

</body>
</html>
```